Bref créative
ZARVEN Skin Care
Bright & Fun-filled
Maribel Dunstan
Owner
none on card
zarvenbodycare@plumtree-mail.com
www.zarvenbodycare-shop.com
Natural Skin Care Solutions

```html
<!DOCTYPE html>
<html lang="en">
<head>
<meta charset="utf-8">
<title>ZARVEN Skin Care – Stationery Set</title>
<link rel="stylesheet" href="https://fonts.googleapis.com/css2?family=Quicksand:wght@400;500&family=Open+Sans:wght@400;600&display=swap">
<style>
  :root {
    --backdrop: #a2a2a2;
    --frame: #cdcdcd;
    --paper: #ffffff;
    --green-light: #8cc63f;
    --green-mid: #5f9e1e;
    --green-dark: #3c7410;
    --logo-grey: #8d8d8d;
    --logo-silver: #d9dcd6;
    --tagline: #5f9e1e;
    --small-text: #ffffff;
    --body-text: #6b6b6b;
  }
  * { box-sizing: border-box; margin: 0; padding: 0; }
  html, body { width: 1200px; height: 684px; overflow: hidden; }
  body { background: var(--backdrop); font-family: "Open Sans", Arial, sans-serif; }
  .canvas {
    position: relative; width: 1200px; height: 684px;
    background: var(--backdrop);
    border: 5px solid var(--frame);
  }
  .green-band {
    background: radial-gradient(ellipse at 50% 50%, var(--green-light) 0%, var(--green-mid) 55%, var(--green-dark) 100%);
  }
  .brand { text-align: center; }
  .brand-name {
    font-family: "Quicksand", sans-serif; font-weight: 400;
    color: var(--logo-grey); letter-spacing: 2px; line-height: 1;
  }
  .brand-tagline {
    font-family: "Open Sans", sans-serif; color: var(--tagline);
    letter-spacing: 1px; text-transform: uppercase;
  }
  .contact-line {
    font-size: 6px; color: var(--small-text); text-align: center; white-space: nowrap;
  }
  .contact-line b { font-weight: 600; }

  /* Letterhead */
  .letterhead {
    position: absolute; left: 187px; top: 36px; width: 437px; height: 619px;
    background: var(--paper); box-shadow: 0 1px 3px rgba(0,0,0,.25);
  }
  .letterhead .header { height: 43px; }
  .letterhead .brand { margin-top: 20px; }
  .letterhead .brand-name { font-size: 26px; }
  .letterhead .brand-tagline { font-size: 5px; margin-top: 3px; }
  .letterhead .footer {
    position: absolute; left: 0; bottom: 0; width: 100%; height: 48px;
    display: flex; align-items: center; justify-content: center;
  }

  /* Business cards */
  .card {
    position: absolute; left: 57px; width: 187px;
    box-shadow: 0 1px 3px rgba(0,0,0,.25); overflow: hidden;
  }
  .card-front { top: 235px; height: 108px; background: var(--paper); }
  .card-front .top-strip { height: 7px; }
  .card-front .person { font-size: 6px; color: var(--body-text); margin: 3px 0 0 10px; }
  .card-front .brand { margin-top: 14px; }
  .card-front .brand-name { font-size: 19px; }
  .card-front .brand-tagline { font-size: 4px; margin-top: 2px; }
  .card-front .details { font-size: 5px; color: var(--body-text); margin: 6px 0 0 10px; line-height: 1.4; }
  .card-front .bottom-strip { position: absolute; left: 0; bottom: 0; width: 100%; height: 14px; }
  .card-back { top: 355px; height: 132px; }
  .card-back .brand { margin-top: 30px; }
  .card-back .brand-name { font-size: 30px; color: var(--logo-silver); }
  .card-back .brand-tagline { font-size: 8px; color: var(--small-text); text-transform: none; letter-spacing: .3px; margin-top: 4px; }
  .card-back .web { font-size: 6px; color: var(--small-text); text-align: center; margin-top: 22px; }

  /* Envelope with flap */
  .envelope-flap {
    position: absolute; left: 638px; top: 91px; width: 533px; height: 180px;
    background: var(--paper); box-shadow: 0 1px 3px rgba(0,0,0,.25);
  }
  .envelope-flap svg { position: absolute; left: 0; top: 0; }
  .envelope-flap .brand { position: absolute; left: 0; top: 34px; width: 100%; }
  .envelope-flap .brand-name { font-size: 26px; color: var(--logo-silver); }

  /* Window envelope */
  .envelope-long {
    position: absolute; left: 638px; top: 360px; width: 533px; height: 225px;
    background: var(--paper); box-shadow: 0 1px 3px rgba(0,0,0,.25);
  }
  .envelope-long .header { height: 62px; }
  .envelope-long .brand { margin-top: 24px; }
  .envelope-long .brand-name { font-size: 24px; }
  .envelope-long .brand-tagline { font-size: 5px; margin-top: 3px; }
  .envelope-long .footer {
    position: absolute; left: 0; bottom: 0; width: 100%; height: 36px;
    display: flex; align-items: center; justify-content: center;
  }
</style>
</head>
<body>
<main class="canvas">

  <section class="letterhead" aria-label="Letterhead">
    <div class="header green-band"></div>
    <div class="brand">
      <div class="brand-name">ZARVEN</div>
      <div class="brand-tagline">Natural Skin Care Solutions</div>
    </div>
    <div class="footer green-band">
      <p class="contact-line"><b>Phone:</b> 555 014 2286 &nbsp;|&nbsp; <b>Email:</b> zarvenbodycare@plumtree-mail.com &nbsp;|&nbsp; <b>Web:</b> www.zarvenbodycare-shop.com</p>
    </div>
  </section>

  <section class="card card-front" aria-label="Business card front">
    <div class="top-strip green-band"></div>
    <p class="person">Maribel Dunstan | Owner</p>
    <div class="brand">
      <div class="brand-name">ZARVEN</div>
      <div class="brand-tagline">Natural Skin Care Solutions</div>
    </div>
    <p class="details">Email: zarvenbodycare@plumtree-mail.com<br>Web: www.zarvenbodycare-shop.com</p>
    <div class="bottom-strip green-band"></div>
  </section>

  <section class="card card-back green-band" aria-label="Business card back">
    <div class="brand">
      <div class="brand-name">ZARVEN</div>
      <div class="brand-tagline">Natural Skin Care Solutions</div>
    </div>
    <p class="web">www.zarvenbodycare-shop.com</p>
  </section>

  <section class="envelope-flap" aria-label="Envelope">
    <svg width="533" height="180" viewBox="0 0 533 180" aria-hidden="true">
      <defs>
        <radialGradient id="flapGreen" cx="50%" cy="35%" r="65%">
          <stop offset="0" stop-color="#8cc63f"/>
          <stop offset="0.55" stop-color="#5f9e1e"/>
          <stop offset="1" stop-color="#3c7410"/>
        </radialGradient>
      </defs>
      <path d="M0 0 H533 V58 Q533 110 478 110 H55 Q0 110 0 58 Z" fill="url(#flapGreen)"/>
    </svg>
    <div class="brand"><div class="brand-name">ZARVEN</div></div>
  </section>

  <section class="envelope-long" aria-label="Business envelope">
    <div class="header green-band"></div>
    <div class="brand">
      <div class="brand-name">ZARVEN</div>
      <div class="brand-tagline">Natural Skin Care Solutions</div>
    </div>
    <div class="footer green-band">
      <p class="contact-line"><b>Phone:</b> 555 014 2286 &nbsp;|&nbsp; <b>Email:</b> zarvenbodycare@plumtree-mail.com &nbsp;|&nbsp; <b>Web:</b> www.zarvenbodycare-shop.com</p>
    </div>
  </section>

</main>
</body>
</html>
```